"Vine Hollow Excursions" is a top notch Santa Barbara County Wine Tour company.

We provide scenic, boutique and custom wine tours. I need the card to be clean and classy. I will provide our logo. I would like the logo to cover the back side of the card as an option and would like to see a couple color options other then our signature green and gold. I would like to see some creative options and let the designers come up with options.
I need cards for myself and my team. The final design should communicate "An authentic and boutique wine tour experience"
Please use my website for reference www.vinehollowexcursions.example

Target Market(s)

We have a wide range of clients from millennials to baby boomers

Industry/Entity Type

Tour

Contact Information for Business Card

Contact info:
Dale Morton
805-219-6384
info@vinehollowexcursions.example
vinehollowexcursions.example

Colors

Designer to choose colors to be used in the design.

Requirements
Must have
• my logo
Nice to have
• *I would like to have the backside side with the logo and the company statement
• "An authentic and boutique wine tour experience" as an option.
• *I would also like to see what the designers can create!
• *I would like to see an option that incorporates or social: instagram, yelp, trip advisor
Should not have
• I do not want it too busy.

```html
<!DOCTYPE html>
<html lang="en">
<head>
<meta charset="utf-8">
<title>Vine Hollow Excursions – Business Card</title>
<link href="https://fonts.googleapis.com/css2?family=Roboto:wght@400;500;700&display=swap" rel="stylesheet">
<style>
  :root {
    --backdrop: #e9e4dc;
    --card: #f7f7f5;
    --card-edge: #dcdcd8;
    --brand-green: #1f6b3a;
    --brand-gold: #a88a5c;
    --text-grey: #4a4a4a;
    --social-a: #8a6a4a;
    --social-b: #3f8f2e;
    --social-c: #d8231f;
  }
  * { box-sizing: border-box; margin: 0; padding: 0; }
  html, body {
    width: 1200px;
    height: 800px;
    overflow: hidden;
    background: var(--backdrop);
    font-family: "Roboto", Arial, sans-serif;
  }
  .canvas {
    position: relative;
    width: 1200px;
    height: 800px;
  }
  .card {
    position: absolute;
    width: 525px;
    height: 300px;
    background: var(--card);
    border: 1px solid var(--card-edge);
    border-radius: 3px;
    box-shadow: 0 10px 28px rgba(0,0,0,0.14);
  }
  /* Contact side */
  .card--contact { left: 55px; top: 110px; }
  .contact {
    position: absolute;
    left: 58px;
    top: 92px;
  }
  .contact__name {
    color: var(--brand-green);
    font-weight: 700;
    font-size: 22px;
    letter-spacing: 0.3px;
    text-transform: uppercase;
    margin-bottom: 14px;
  }
  .contact__row {
    font-size: 14px;
    text-transform: uppercase;
    color: var(--text-grey);
    line-height: 28px;
    letter-spacing: 0.2px;
  }
  .contact__label {
    color: var(--brand-green);
    font-weight: 700;
    margin-right: 4px;
  }
  /* Brand side */
  .card--brand { left: 620px; top: 390px; }
  .social {
    position: absolute;
    top: 22px;
    right: 24px;
    display: flex;
    gap: 5px;
  }
  .social__tile {
    width: 26px;
    height: 26px;
    border-radius: 4px;
  }
  .social__tile--a { background: var(--social-a); }
  .social__tile--b { background: var(--social-b); }
  .social__tile--c { background: var(--social-c); }
  .brand {
    position: absolute;
    left: 0;
    right: 0;
    top: 78px;
    text-align: center;
  }
  .brand__mark {
    display: block;
    margin: 0 auto 14px;
  }
  .brand__name {
    color: var(--brand-gold);
    font-weight: 500;
    font-size: 27px;
    letter-spacing: 1.5px;
    text-transform: uppercase;
  }
  .brand__region {
    margin-top: 6px;
    color: var(--brand-green);
    font-size: 11px;
    letter-spacing: 6px;
    text-transform: uppercase;
  }
  .tagline {
    position: absolute;
    left: 0;
    right: 0;
    bottom: 46px;
    text-align: center;
    color: var(--text-grey);
    font-size: 15px;
  }
</style>
</head>
<body>
  <main class="canvas">
    <section class="card card--contact" aria-label="Contact side">
      <div class="contact">
        <p class="contact__name">Dale Morton</p>
        <p class="contact__row"><span class="contact__label">Phone:</span>805-219-6384</p>
        <p class="contact__row"><span class="contact__label">Email:</span>info@vinehollowexcursions.example</p>
        <p class="contact__row"><span class="contact__label">Web:</span>vinehollowexcursions.example</p>
      </div>
    </section>

    <section class="card card--brand" aria-label="Brand side">
      <div class="social" aria-label="Social listings">
        <span class="social__tile social__tile--a"></span>
        <span class="social__tile social__tile--b"></span>
        <span class="social__tile social__tile--c"></span>
      </div>
      <div class="brand">
        <svg class="brand__mark" width="40" height="40" viewBox="0 0 40 40" aria-hidden="true">
          <circle cx="20" cy="20" r="18" fill="var(--brand-green)"/>
        </svg>
        <p class="brand__name">Vine Hollow Excursions</p>
        <p class="brand__region">Santa Barbara County</p>
      </div>
      <p class="tagline">An authentic &amp; boutique wine tour experience</p>
    </section>
  </main>
</body>
</html>
```